Professional & attention grabbing.

A business card design, front and back. I already have a logo I will attach, but I am open to something new as well.
Things to include:
Name:
Title:
Phone:
Email:
Wanting something that is professional but attention grabbing.
Also we do a lot of work using drones on natural gas pipelines (leading the future)if you want to include any of that. I'm open to ideas.
Target Market(s)
Natural gas transmission industry / greenhouse gas mitigation industry
Industry/Entity Type
Business
Colors
Designer to choose colors to be used in the design.
Look and feel
Each slider illustrates characteristics of the customer's brand and the style your logo design should communicate.

```html
<!DOCTYPE html>
<html lang="en">
<head>
<meta charset="utf-8">
<title>Kelvra Inspections – Business Card</title>
<link rel="stylesheet" href="https://fonts.googleapis.com/css2?family=Roboto+Condensed:wght@300;400;700&display=swap">
<style>
  :root {
    --page-bg: #1e1e1e;
    --card-white: #ffffff;
    --brand-red: #c81f26;
    --brand-red-dark: #9e161c;
    --swoosh-gray: #3a3a3c;
    --text-dark: #3a3a3c;
    --back-top: #4a4a4c;
    --back-bottom: #1c1c1d;
    --on-dark: #ffffff;
    --muted-on-dark: #bdbdbd;
  }
  html, body {
    margin: 0;
    padding: 0;
    width: 1200px;
    height: 950px;
    overflow: hidden;
    background: var(--page-bg);
    font-family: "Roboto Condensed", "Arial Narrow", sans-serif;
  }
  .canvas {
    position: relative;
    width: 1200px;
    height: 950px;
  }
  .card {
    position: absolute;
    left: 230px;
    width: 740px;
    height: 420px;
    overflow: hidden;
    border-radius: 4px;
    box-shadow: 0 10px 30px rgba(0,0,0,.45);
  }
  .card-front { top: 40px; background: var(--card-white); }
  .card-back {
    top: 490px;
    background: linear-gradient(135deg, var(--back-top) 0%, #2c2c2d 55%, var(--back-bottom) 100%);
  }
  .front-art { position: absolute; inset: 0; }

  .holder {
    position: absolute;
    top: 18px;
    right: 34px;
    text-align: right;
    color: var(--on-dark);
    text-transform: uppercase;
    line-height: 1.1;
  }
  .holder-name { font-weight: 700; font-size: 26px; letter-spacing: .5px; }
  .holder-title { font-weight: 300; font-size: 18px; letter-spacing: .5px; }

  .brand {
    display: flex;
    align-items: center;
    gap: 10px;
    color: var(--text-dark);
    font-weight: 700;
    text-transform: uppercase;
    white-space: nowrap;
  }
  .brand-mark {
    width: 18px;
    height: 18px;
    background: var(--brand-red);
  }
  .card-front .brand {
    position: absolute;
    left: 220px;
    top: 250px;
    font-size: 40px;
  }

  .contact {
    position: absolute;
    left: 222px;
    top: 318px;
    margin: 0;
    padding: 0;
    list-style: none;
    color: var(--text-dark);
    font-size: 18px;
    font-weight: 400;
  }
  .contact li {
    display: flex;
    align-items: center;
    gap: 10px;
    height: 26px;
  }
  .contact-icon { width: 14px; height: 14px; flex: none; }

  .card-back .brand {
    position: absolute;
    left: 0;
    right: 0;
    top: 176px;
    justify-content: center;
    color: var(--on-dark);
    font-size: 56px;
  }
  .back-web {
    position: absolute;
    left: 0;
    right: 0;
    bottom: 34px;
    text-align: center;
    color: var(--muted-on-dark);
    font-size: 15px;
    font-weight: 300;
    letter-spacing: 7px;
  }
</style>
</head>
<body>
<main class="canvas">

  <section class="card card-front" aria-label="Business card front">
    <svg class="front-art" viewBox="0 0 740 420" width="740" height="420" aria-hidden="true">
      <path d="M0,0 H740 V70 C560,78 360,100 240,150 C150,188 70,205 0,210 Z" fill="var(--brand-red)"/>
      <path d="M0,0 H260 C170,40 70,60 0,70 Z" fill="var(--brand-red-dark)" opacity=".35"/>
      <path d="M0,224 C90,220 170,200 252,160 C185,214 100,246 0,256 Z" fill="var(--swoosh-gray)"/>
    </svg>

    <div class="holder">
      <div class="holder-name">Mark Ellis</div>
      <div class="holder-title">President</div>
    </div>

    <div class="brand"><span class="brand-mark"></span>Kelvra Inspections</div>

    <ul class="contact">
      <li>
        <svg class="contact-icon" viewBox="0 0 14 14" aria-hidden="true">
          <circle cx="7" cy="7" r="7" fill="var(--brand-red)"/>
          <path d="M4.3,3.6 L5.6,3.4 L6.2,5 L5.4,5.7 C5.9,6.8 6.7,7.7 7.9,8.3 L8.6,7.6 L10.2,8.2 L10,9.6 C7,10 3.8,6.9 4.3,3.6 Z" fill="#fff"/>
        </svg>
        555 0142 7781
      </li>
      <li>
        <svg class="contact-icon" viewBox="0 0 14 14" aria-hidden="true">
          <circle cx="7" cy="7" r="7" fill="var(--brand-red)"/>
          <rect x="3.5" y="4.5" width="7" height="5" fill="#fff"/>
          <path d="M3.5,4.5 L7,7.3 L10.5,4.5" fill="none" stroke="var(--brand-red)" stroke-width=".8"/>
        </svg>
        mark@kelvra.com
      </li>
      <li>
        <svg class="contact-icon" viewBox="0 0 14 14" aria-hidden="true">
          <circle cx="7" cy="7" r="7" fill="var(--brand-red)"/>
          <circle cx="7" cy="7" r="3.3" fill="none" stroke="#fff" stroke-width="1"/>
          <path d="M3.7,7 H10.3" stroke="#fff" stroke-width=".8"/>
        </svg>
        www.kelvra.com
      </li>
    </ul>
  </section>

  <section class="card card-back" aria-label="Business card back">
    <div class="brand">Kelvra Inspections</div>
    <div class="back-web">www.kelvra.com</div>
  </section>

</main>
</body>
</html>
```